Harbourline Electrical Solutions

On one side. LOGO (underneath:) Commercial Industrial Residential

- NAME & CONTACT DETAILS

Marcus T. Hollings
Project Manager

(Cell icon) (441) 555-0187
(Email icon) hlelectricalsolutions@mailvento.com
(Facebook & Instagram icons )@hlelectricalsolutions

Other side: LOGO - underneath ELECTRICAL CONSTRUCTION & MAINTENANCE . LED LIGHTING & AUTOMATION . LIFE SAFETY SYSTEMS (FIRE ALARM / SECURITY) . DATA & COMMUNICATION

```html
<!DOCTYPE html>
<html lang="en">
<head>
<meta charset="utf-8">
<title>Harbourline Electrical Solutions – Business Card</title>
<link rel="stylesheet" href="https://fonts.googleapis.com/css2?family=Montserrat:wght@500;600;700&family=Work+Sans:wght@400;500&display=swap">
<style>
  :root {
    --teal: #0f5a70;
    --white: #ffffff;
    --paper: #e4e4e4;
    --grey-text: #6f7477;
  }
  html, body {
    margin: 0;
    padding: 0;
    width: 1200px;
    height: 930px;
    overflow: hidden;
    background: var(--paper);
  }
  .canvas {
    position: relative;
    width: 1200px;
    height: 930px;
  }
  .card {
    position: absolute;
    width: 560px;
    height: 320px;
    border-radius: 22px;
    overflow: hidden;
    box-shadow: 0 6px 18px rgba(0,0,0,0.18);
  }

  /* Back side */
  .card--back {
    left: 90px;
    top: 110px;
    background: var(--teal);
    color: var(--white);
    font-family: "Montserrat", sans-serif;
  }
  .brand {
    position: absolute;
    left: 70px;
    top: 62px;
    display: flex;
    align-items: center;
    gap: 16px;
  }
  .brand__mark {
    width: 26px;
    height: 26px;
    background: var(--white);
  }
  .brand__name {
    padding-left: 16px;
    border-left: 2px solid var(--white);
    font-weight: 600;
    font-size: 24px;
    line-height: 1.15;
    letter-spacing: 2px;
    text-transform: uppercase;
  }
  .services {
    position: absolute;
    left: 70px;
    top: 190px;
    margin: 0;
    padding: 0;
    list-style: none;
    font-weight: 600;
    font-size: 14px;
    letter-spacing: 1px;
    line-height: 24px;
    text-transform: uppercase;
  }
  .services li::before {
    content: "";
    display: inline-block;
    width: 6px;
    height: 6px;
    border-radius: 50%;
    background: var(--white);
    margin-right: 12px;
    vertical-align: middle;
  }

  /* Front side */
  .card--front {
    left: 550px;
    top: 500px;
    background: var(--white);
  }
  .band {
    position: absolute;
    left: 0;
    top: 0;
  }
  .band__brand {
    position: absolute;
    left: 28px;
    top: 296px;
    transform: rotate(-90deg);
    transform-origin: left top;
    display: flex;
    align-items: center;
    gap: 12px;
    color: var(--white);
    font-family: "Montserrat", sans-serif;
    font-weight: 600;
    font-size: 13px;
    letter-spacing: 1.5px;
    line-height: 1.25;
    text-transform: uppercase;
    white-space: nowrap;
  }
  .band__mark {
    width: 22px;
    height: 22px;
    background: var(--white);
  }
  .band__name {
    padding-left: 12px;
    border-left: 1.5px solid var(--white);
  }
  .person {
    position: absolute;
    left: 215px;
    top: 44px;
  }
  .person__name {
    margin: 0;
    font-family: "Montserrat", sans-serif;
    font-weight: 700;
    font-size: 25px;
    letter-spacing: 0.5px;
    color: var(--teal);
    text-transform: uppercase;
  }
  .person__role {
    margin: 2px 0 0;
    font-family: "Work Sans", sans-serif;
    font-size: 14px;
    color: var(--grey-text);
  }
  .contact {
    position: absolute;
    left: 258px;
    right: 24px;
    top: 176px;
    font-family: "Work Sans", sans-serif;
    font-size: 13.5px;
    color: var(--grey-text);
  }
  .contact__rule {
    height: 1px;
    background: var(--teal);
    margin: 0 0 14px;
  }
  .contact__row {
    display: flex;
    align-items: center;
    gap: 8px;
    height: 24px;
    white-space: nowrap;
  }
  .icon {
    width: 16px;
    height: 16px;
    border-radius: 3px;
    background: var(--teal);
    flex: none;
  }
  .contact__social {
    margin-top: 14px;
    padding-top: 14px;
    border-top: 1px solid var(--teal);
  }
</style>
</head>
<body>
<div class="canvas">

  <section class="card card--back" aria-label="Card back">
    <div class="brand">
      <span class="brand__mark"></span>
      <span class="brand__name">Harbourline<br>Electrical<br>Solutions</span>
    </div>
    <ul class="services">
      <li>Data &amp; Communication</li>
      <li>LED Lighting &amp; Automation</li>
      <li>Electrical Construction &amp; Maintenance</li>
      <li>Life Safety Systems (Fire Alarm / Security)</li>
    </ul>
  </section>

  <section class="card card--front" aria-label="Card front">
    <svg class="band" width="560" height="320" viewBox="0 0 560 320" aria-hidden="true">
      <polygon points="0,0 115,0 185,40 140,55 245,320 0,320" fill="var(--teal)"/>
    </svg>
    <div class="band__brand">
      <span class="band__mark"></span>
      <span class="band__name">Harbourline<br>Electrical<br>Solutions</span>
    </div>

    <div class="person">
      <h1 class="person__name">Marcus T. Hollings</h1>
      <p class="person__role">Project Manager</p>
    </div>

    <div class="contact">
      <div class="contact__rule"></div>
      <div class="contact__row">
        <svg class="icon" viewBox="0 0 16 16" aria-label="Phone">
          <rect width="16" height="16" rx="3" fill="var(--teal)"/>
          <path d="M5 3.5l1.6 2.2-1 1.1c.6 1.4 1.6 2.4 3 3l1.1-1 2.2 1.6-.9 1.9C7.5 12.2 3.8 8.5 3.3 4.4z" fill="#fff"/>
        </svg>
        <span>(441) 555-0187</span>
      </div>
      <div class="contact__row">
        <svg class="icon" viewBox="0 0 16 16" aria-label="Email">
          <rect width="16" height="16" rx="3" fill="var(--teal)"/>
          <rect x="3.5" y="5" width="9" height="6.5" fill="none" stroke="#fff" stroke-width="1.2"/>
          <path d="M3.5 5l4.5 3.6L12.5 5" fill="none" stroke="#fff" stroke-width="1.2"/>
        </svg>
        <span>hlelectricalsolutions@mailvento.com</span>
      </div>
      <div class="contact__row contact__social">
        <span class="icon" aria-hidden="true"></span>
        <span class="icon" aria-hidden="true"></span>
        <span>@hlelectricalsolutions</span>
      </div>
    </div>
  </section>

</div>
</body>
</html>
```